Request for Business Card Design

Hi. My name is Marlene, I am looking for a new business card design for my company, Quarrow Signal Instruments, LLC. I really like the design you did for Tarsel Venture and was hoping you could do something similar using our full logo and our mark. I am also open to any raised texture design using our mark. I have attached our full logo, which would need to be somewhere on the card, as well as the mark in both outline and full form, as well as our brand colors / guide. The card does not have to be white, as long as our logo and mark appear. I actually like darker colored business cards more, but am open to all options. If you are interested in working with me, please let me know. We would also take the business card design into letterhead design if you can do that.

```html
<!DOCTYPE html>
<html lang="en">
<head>
<meta charset="utf-8">
<title>Quarrow Signal Instruments — Business Card</title>
<link href="https://fonts.googleapis.com/css2?family=Montserrat:wght@400;500;700&display=swap" rel="stylesheet">
<style>
  :root {
    --backdrop: #2b2b2e;
    --card: #1b1b1d;
    --brand-blue: #1a9fce;
    --ink-light: #f2f2f2;
    --ink-muted: #d6d6d6;
  }
  * { box-sizing: border-box; margin: 0; padding: 0; }
  html, body {
    width: 1200px; height: 900px; overflow: hidden;
    background: var(--backdrop);
    font-family: "Montserrat", sans-serif;
  }
  .stage {
    width: 1200px; height: 900px;
    display: flex; flex-direction: column;
    align-items: center; justify-content: center; gap: 56px;
  }
  .card {
    width: 600px; height: 343px;
    background: var(--card);
    border-radius: 20px;
    position: relative;
    box-shadow: 0 14px 34px rgba(0,0,0,.45);
  }
  .brand { display: flex; align-items: center; }
  .brand__dot {
    border-radius: 50%;
    background: var(--brand-blue);
    flex: none;
  }
  .brand__name {
    color: var(--ink-light);
    font-weight: 700;
    text-transform: uppercase;
    line-height: 1.15;
  }
  /* info side */
  .card--info .brand {
    position: absolute; left: 40px; top: 150px;
  }
  .card--info .brand__dot { width: 46px; height: 46px; margin-right: 14px; }
  .card--info .brand__name { font-size: 17px; letter-spacing: .5px; width: 200px; }
  .divider {
    position: absolute; left: 300px; top: 90px;
    width: 1.5px; height: 163px; background: var(--brand-blue);
  }
  .contact {
    position: absolute; left: 326px; top: 92px;
    color: var(--ink-muted); font-size: 12.5px;
  }
  .contact__name {
    color: var(--brand-blue); font-weight: 700; font-size: 24px; line-height: 1.05;
  }
  .contact__role { font-size: 14px; margin: 3px 0 10px; color: var(--ink-light); }
  .contact__list { list-style: none; }
  .contact__list li { display: flex; align-items: center; gap: 9px; margin-bottom: 5px; }
  .contact__list svg { width: 12px; height: 12px; fill: var(--brand-blue); flex: none; }
  .contact__address { margin-top: 12px; line-height: 1.45; }
  /* logo side */
  .card--logo .brand {
    position: absolute; left: 0; right: 0; top: 0; bottom: 0; justify-content: center;
  }
  .card--logo .brand__dot { width: 78px; height: 78px; margin-right: 22px; }
  .card--logo .brand__name { font-size: 30px; letter-spacing: 1px; width: 320px; }
</style>
</head>
<body>
<main class="stage">
  <section class="card card--info" aria-label="Business card, contact side">
    <div class="brand">
      <span class="brand__dot"></span>
      <span class="brand__name">Quarrow Signal Instruments</span>
    </div>
    <span class="divider"></span>
    <div class="contact">
      <p class="contact__name">Dorian Vale</p>
      <p class="contact__role">Owner</p>
      <ul class="contact__list">
        <li>
          <svg viewBox="0 0 24 24" aria-hidden="true"><path d="M6.6 10.8a15.1 15.1 0 0 0 6.6 6.6l2.2-2.2a1 1 0 0 1 1-.25 11.4 11.4 0 0 0 3.6.57 1 1 0 0 1 1 1V20a1 1 0 0 1-1 1A17 17 0 0 1 3 4a1 1 0 0 1 1-1h3.5a1 1 0 0 1 1 1c0 1.25.2 2.46.57 3.6a1 1 0 0 1-.25 1z"/></svg>
          +001 555 014 2290
        </li>
        <li>
          <svg viewBox="0 0 24 24" aria-hidden="true"><path d="M2 5h20v14H2z M2 5l10 8 10-8" fill="none" stroke="#1a9fce" stroke-width="2.4"/></svg>
          info@quarrowsignal.com
        </li>
        <li>
          <svg viewBox="0 0 24 24" aria-hidden="true"><circle cx="12" cy="12" r="9" fill="none" stroke="#1a9fce" stroke-width="2.4"/><path d="M3 12h18M12 3c3 3 3 15 0 18M12 3c-3 3-3 15 0 18" fill="none" stroke="#1a9fce" stroke-width="1.8"/></svg>
          www.quarrowsignal.com
        </li>
      </ul>
      <p class="contact__address">1180 Halvern Park Road<br>Cedar Bluff, CO 80999</p>
    </div>
  </section>

  <section class="card card--logo" aria-label="Business card, logo side">
    <div class="brand">
      <span class="brand__dot"></span>
      <span class="brand__name">Quarrow Signal Instruments</span>
    </div>
  </section>
</main>
</body>
</html>
```